Web Design for Webdesign company 3 page PSD

Project
---------
We need a PSD Web Design to be used in a WordPress installation.
What we would like to create is a professional looking website for a web design agency. We also need you to look for suitable stock images to be placed on these pages.
We need the design for:
Homepage
Landing page
Contact page
attached in the pages file you will find a file with more in depth details how these files should be build up.
We would like to see a desktop version and a mobile version of these pages
The website should have a 1100px width.
The mobile design should have 480px width.
The homepage should have a header slider about 450px high.
The slider is preferred full width and should have some images text and a button
Objectives
-------------
The main objective for the website is to get leads from customers in the form of a request for a quotation or a call or mail me back action. The most important action for the homepage is to link and navigate to our landing pages.
What we want to tell our visitors (our main products)
-------------------------------------------------------------------
- A website with no big investment but a monthly rate
- A successful website with no worries (a complete website, seo, hosting and a service contract for future customization is included for a monthly rate)
Color Scheme
------------
Use branding colors. You can find them in the branding.pdf file.
Additional colors:
White: #ffffff
Black: #181818
Company info
--------------
We are a starting web design / marketing agency based in The Netherlands and looking for the design of our website. Our services are (custom) webdesign, website marketing or combinations of both. Our main customer group is small business owners.
We sell websites but give the option to buy it with a lease contract.
A second product is a default website with a complete service: SEO, hosting and a service contract for a monthly rate.
Content:
-----------
If not available place Lorem Ipsum text.
There will come about 400 words of text on the landing pages
Design Competition
--------------------------
Since this is a designing competition we would like to see your creativity.
What you can expect from us is a lot of feedback 7 days a week with short response time.
You can send us the first sketchy mock ups of the homepage and we will give feedback based on these design. But we like your feedback or comments as well
Read the pages file for more in depth details how the pages should be designed

Target Market(s)
Small business owners in The Netherlands
Industry/Entity Type
It Company
Number of Pages Required
3 page
Requirements
Must have
- Homepage:
- Header slider with images, some text and a link to a custom page
- The slider should have 3 designed slides
- Landings page:
- Sidebar
- Action button for a request for a quotation
- Action button for a call me back action
- Action button for an appointment
- Contact form:
- Address details
- Contact form
Nice to have
- Homepage:
- Full width slider
- Testimonial block
- Blog items
Should not have
- Flash
- A to crowded design

```html
<!DOCTYPE html>
<html lang="en">
<head>
<meta charset="utf-8">
<title>Northvale Web Services – Contact</title>
<link href="https://fonts.googleapis.com/css2?family=Open+Sans:wght@400;600&family=Arimo:wght@400;700&display=swap" rel="stylesheet">
<style>
:root{
  --brand:#5e9a7b;
  --brand-teal:#4b8a82;
  --ink:#222222;
  --text:#555555;
  --panel:#ebebeb;
  --white:#ffffff;
  --nav-pill:#5a5a5a;
  --btn-dark:#2e2e2e;
  --footer:#323232;
  --footer-bottom:#262626;
  --footer-text:#bdbdbd;
  --line:#d6d6d6;
  --mark:#8a8a8a;
}
*{box-sizing:border-box;margin:0;padding:0}
html,body{width:985px;height:1200px;overflow:hidden;background:var(--white)}
body{position:relative;font-family:"Open Sans",Arial,sans-serif;color:var(--text);font-size:12px}
.abs{position:absolute}
h2,h3,.nav a,.btn{font-family:"Arimo",Arial,sans-serif}

/* header */
.site-header{position:absolute;left:0;top:0;width:985px;height:89px;background:var(--white)}
.brand{position:absolute;left:76px;top:33px;display:flex;align-items:center;gap:10px}
.brand-mark{width:24px;height:24px;background:var(--mark)}
.brand-name{font-family:"Open Sans",Arial,sans-serif;font-weight:600;font-size:17px;color:var(--ink);white-space:nowrap}
.nav a{position:absolute;top:33px;display:block;font-size:12.5px;font-weight:700;color:#444;text-decoration:none;height:25px;line-height:25px;letter-spacing:.2px;white-space:nowrap}
.nav a.active{background:var(--nav-pill);color:var(--white);border-radius:13px;width:91px;text-align:center}

/* banner */
.page-banner{position:absolute;left:0;top:89px;width:985px;height:76px;
  background:linear-gradient(90deg,#5e9a78 0%,#66a27f 30%,#3e7053 48%,#6aa885 58%,#3d6a52 72%,#6aa684 86%,#5b9473 100%)}
.page-banner h1{position:absolute;left:75px;top:28px;font-family:"Arimo",Arial,sans-serif;font-size:19px;font-weight:700;color:var(--white)}
.intro{left:74px;top:183px;width:830px;line-height:19px;font-size:11.2px}

/* panels */
.panel{position:absolute;background:var(--panel)}
.panel-enquiry{left:75px;top:248px;width:553px;height:600px}
.panel-map{left:651px;top:248px;width:258px;height:403px}
.panel h2{position:absolute;font-size:14px;font-weight:700;color:var(--ink);letter-spacing:.3px}
.panel p{position:absolute;font-size:11.2px;line-height:17px}

.choices{position:absolute;left:23px;top:115px;list-style:none}
.choices li{display:flex;align-items:center;height:28px;font-size:11.5px}
.radio{width:9px;height:9px;border:1px solid #aaa;border-radius:50%;margin-right:7px;background:var(--white);position:relative}
.radio.on::after{content:"";position:absolute;left:2px;top:2px;width:3px;height:3px;border-radius:50%;background:#333}

.field{position:absolute;left:23px;width:315px;height:27px;background:var(--white);border:1px solid var(--line);border-radius:3px;display:flex;align-items:center;padding-left:7px;color:#aaa;font-size:11px}
.field svg{margin-right:7px;flex:none}
.field.message{height:103px;align-items:flex-start;padding-top:7px}
.attach-label{position:absolute;left:23px;top:505px;font-size:11px}
.attach{position:absolute;left:115px;top:499px;width:223px;height:27px;display:flex;border:1px solid var(--line);border-radius:3px;overflow:hidden}
.attach span{flex:1;background:var(--white)}
.attach b{width:72px;background:var(--btn-dark);color:var(--white);font-family:"Arimo",Arial,sans-serif;font-weight:400;font-size:12px;text-align:center;line-height:25px}
.btn{position:absolute;background:var(--brand);color:var(--white);font-weight:700;font-size:12.5px;text-align:center;border-radius:2px;letter-spacing:.3px}
.btn-submit{left:23px;top:550px;width:88px;height:27px;line-height:27px}

.info{position:absolute;left:370px;display:flex;gap:9px;font-size:11px;line-height:17px}
.info svg{flex:none;margin-top:3px}
.info.phone{font-size:14.5px;font-weight:600;color:var(--ink);align-items:center}

.map{position:absolute;left:8px;top:179px;width:242px;height:216px;border:4px solid var(--white);
  background:linear-gradient(135deg,#e7e2cf 0%,#dfe6c8 40%,#c9dcb7 60%,#e8e3cf 100%)}

/* footer */
.site-footer{position:absolute;left:0;top:893px;width:985px;height:247px;background:var(--footer)}
.site-footer h3{position:absolute;color:var(--white);font-size:12.5px;font-weight:700;letter-spacing:.2px;line-height:16px}
.news-input{position:absolute;left:76px;width:198px;height:26px;background:var(--white);border-radius:2px;color:#888;font-size:11px;line-height:26px;padding-left:7px}
.btn-subscribe{left:76px;top:165px;width:198px;height:26px;line-height:26px;background:var(--brand-teal)}
.quick{position:absolute;left:333px;top:72px;list-style:none}
.quick li{font-size:11.5px;color:var(--footer-text);height:19.7px}
.f-info{position:absolute;left:502px;display:flex;gap:11px;color:var(--footer-text);font-size:11.5px;line-height:16px}
.f-info svg{flex:none;margin-top:2px}
.social{position:absolute;left:724px;display:flex;align-items:center;gap:8px;color:var(--footer-text);font-size:11.5px}
.social i{width:22px;height:22px;border:2px solid #9a9a9a;border-radius:50%}
.legal{position:absolute;left:0;top:1140px;width:985px;height:60px;background:var(--footer-bottom);text-align:center;color:var(--footer-text);font-size:11.5px;line-height:18px;padding-top:11px}
</style>
</head>
<body>

<header class="site-header">
  <div class="brand"><span class="brand-mark"></span><span class="brand-name">Northvale Web Services</span></div>
  <nav class="nav">
    <a href="#" style="left:484px">HOME</a>
    <a href="#" class="active" style="left:537px">LANDING</a>
    <a href="#" style="left:650px">TESTIMONIALS</a>
    <a href="#" style="left:778px">BLOG</a>
    <a href="#" style="left:849px">CONTACT</a>
  </nav>
</header>

<section class="page-banner"><h1>CONTACT</h1></section>

<p class="abs intro">Duis aute irure dolor in reprehenderit in voluptate velit esse cillum dolore eu fugiat nulla pariatur. Excepteur sint occaecat cupidatat non proident, sunt in culpa qui officia deserunt mollit anim id est laborum.</p>

<section class="panel panel-enquiry">
  <h2 style="left:23px;top:22px">MAKE ENQUIRY</h2>
  <p style="left:23px;top:49px;width:305px">If you like Northvale to help you and would like more information about the cost. Ask for an appointment with one of our specialists.</p>
  <ul class="choices">
    <li><span class="radio"></span>I want to make an appointment</li>
    <li><span class="radio"></span>I want to be called back</li>
    <li><span class="radio on"></span>I want to send a message</li>
  </ul>

  <div class="field" style="top:213px"><svg width="13" height="13" viewBox="0 0 13 13"><path d="M1 12V2h6v10M7 5h5v7M3 4h2M3 7h2M3 10h2M9 7h1M9 10h1" stroke="#aaa" fill="none"/></svg>Comapny Name</div>
  <div class="field" style="top:248px"><svg width="13" height="13" viewBox="0 0 13 13"><circle cx="6.5" cy="4" r="3" fill="#aaa"/><path d="M1 13c0-4 11-4 11 0z" fill="#aaa"/></svg>Contact Name</div>
  <div class="field" style="top:283px"><svg width="13" height="13" viewBox="0 0 13 13"><path d="M1 13V6h4V1h7v12z" fill="none" stroke="#aaa"/><path d="M7 3h3M7 6h3M7 9h3" stroke="#aaa"/></svg>City</div>
  <div class="field" style="top:318px"><svg width="13" height="13" viewBox="0 0 13 13"><circle cx="6.5" cy="6.5" r="5.5" fill="none" stroke="#aaa" stroke-width="1.5"/><circle cx="6.5" cy="6.5" r="2" fill="#aaa"/></svg>Email</div>
  <div class="field" style="top:353px"><svg width="13" height="13" viewBox="0 0 13 13"><path d="M3 1l2 3-1.5 1.5c1 2 2 3 4 4L9 8l3 2-1.5 2.5C6 12 1 7 .5 2.5z" fill="#aaa"/></svg>Phone</div>
  <div class="field message" style="top:388px"><svg width="13" height="13" viewBox="0 0 13 13"><path d="M1 6l5.5-4L12 6v6H1z M1 6l5.5 4L12 6" fill="none" stroke="#aaa"/></svg>Enter Your Message</div>

  <span class="attach-label">Attach File</span>
  <div class="attach"><span></span><b>Open</b></div>
  <div class="btn btn-submit">SUBMIT</div>

  <h2 style="left:371px;top:22px">CONTACT INFO</h2>
  <div class="info" style="top:49px"><svg width="10" height="13" viewBox="0 0 10 13"><path d="M5 13S0 7 0 5a5 5 0 0110 0c0 2-5 8-5 8z" fill="#777"/><circle cx="5" cy="5" r="1.8" fill="var(--panel)"/></svg><span>258, Lorem Ipsum dolor<br>Dosis amet sit - 558895</span></div>
  <div class="info phone" style="top:100px"><svg width="12" height="12" viewBox="0 0 13 13"><path d="M3 1l2 3-1.5 1.5c1 2 2 3 4 4L9 8l3 2-1.5 2.5C6 12 1 7 .5 2.5z" fill="#555"/></svg><span>(800) 555-26-4410</span></div>
  <div class="info" style="top:135px"><svg width="12" height="11" viewBox="0 0 13 12"><path d="M1 5l5.5-4L12 5v6H1z M1 5l5.5 4L12 5" fill="none" stroke="#666" stroke-width="1.3"/></svg><span>info@northvale.example</span></div>
</section>

<aside class="panel panel-map">
  <h2 style="left:23px;top:22px">LOCATION MAP</h2>
  <p style="left:23px;top:49px;width:222px;line-height:19px">Duis aute irure dolor in reprehenderit in voluptate velit esse cillum dolore eu fugiat nulla pariatur. Excepteur sint occaecat cupidatat non proident, sunt in culpa qui officia deserunt mollit anim id est laborum.</p>
  <div class="map" role="img" aria-label="Street map showing the office location"></div>
</aside>

<footer class="site-footer">
  <h3 style="left:76px;top:45px;font-size:14px">SUBSCRIBE TO<br>OUR NEWSLETTER</h3>
  <div class="news-input" style="top:97px">Enter Your Name</div>
  <div class="news-input" style="top:131px">Enter Your Email</div>
  <div class="btn btn-subscribe">SUBSCRIBE</div>

  <h3 style="left:333px;top:45px">QUICK LINKS</h3>
  <ul class="quick"><li>Home</li><li>Landing</li><li>Testimonials</li><li>Blog</li><li>Contact</li></ul>

  <h3 style="left:502px;top:45px">CONTACT INFO</h3>
  <div class="f-info" style="top:73px"><svg width="10" height="13" viewBox="0 0 10 13"><path d="M5 13S0 7 0 5a5 5 0 0110 0c0 2-5 8-5 8z" fill="#aaa"/><circle cx="5" cy="5" r="1.8" fill="var(--footer)"/></svg><span>228, lorem ipsum dolor sit,<br>dosis miunf- 845848</span></div>
  <div class="f-info" style="top:119px"><svg width="11" height="11" viewBox="0 0 13 13"><path d="M3 1l2 3-1.5 1.5c1 2 2 3 4 4L9 8l3 2-1.5 2.5C6 12 1 7 .5 2.5z" fill="#aaa"/></svg><span>Phone: (800)555-26-4410<br>Fax: (800)555-26-4411</span></div>
  <div class="f-info" style="top:163px"><svg width="12" height="11" viewBox="0 0 13 12"><path d="M1 5l5.5-4L12 5v6H1z M1 5l5.5 4L12 5" fill="none" stroke="#aaa" stroke-width="1.3"/></svg><span>Email: info@northvale.example<br>Website:www.northvale.example</span></div>

  <h3 style="left:724px;top:45px">STAY CONNECTED</h3>
  <div class="social" style="top:71px"><i></i>Follow Us On Newsfeed</div>
  <div class="social" style="top:110px"><i></i>Follow Us On Updates</div>
  <div class="social" style="top:149px"><i></i>Follow Us On Network</div>
</footer>

<div class="legal">© 2015 Northvale All Rights Reserved.<br>Terms of Use | Legal Disclaimer | Privacy Policy | References</div>

</body>
</html>
```